Harborview Estates Business Card for Apartment Buildings

Create business cards for resident managers who run apartment buildings. The audience is the public who are searching for apartment rentals, and current residents who live at the apartment building. Key design element will be incorporating the company logo, however, the logo cannot dominate. The building name and manager name are more important than the logo. Current business card design leaves little room for copy, so we may need to reduce the size on the current card to allow for more space for copy.

Target Market(s)

Adults 18-65 years of age, who are looking for an apartment rental, plus current residents who live at our apartment buildings.

Industry/Entity Type

Property Management

Contact Information for Business Card

A major design element will be use of the company logo. Important property and manager contact information must be part of the design. The size of the logo will need to be reduced to make room for building and manager contact copy.

Font styles to use
Sans Serif

Colors
3176b5
000000
959595
ffffff

Requirements
Must have
• 1) Incorporate the company logo.
• 2) Use the company colors (dark blue, black/grey, over white).
• 3) FEATURE THE BUILDING NAME
• 4) FEATURE THE MANAGER NAME
• 5) The company name is less important than BUILDING and MANAGER
• 6) Manager contact information
• **SEE ATTACHED CREATIVE BRIEF**
Nice to have
• 1) Back of card logo watermark
• 2) Ability to write notes on back of carfd
Should not have
• Avoid letting the company logo dominate the card, the building name and manager are more important than the company logo.

```html
<!DOCTYPE html>
<html lang="en">
<head>
<meta charset="utf-8">
<title>Harborview Estates Business Card</title>
<link href="https://fonts.googleapis.com/css2?family=Arimo:wght@400;700&display=swap" rel="stylesheet">
<style>
  :root {
    --brand-blue: #1a6aaa;
    --ink: #222222;
    --mist-grey: #e6e6e6;
    --paper: #ffffff;
    --backdrop: #eeeeec;
  }
  html, body {
    margin: 0;
    padding: 0;
    width: 1200px;
    height: 900px;
    overflow: hidden;
    background: var(--backdrop);
    font-family: "Arimo", Arial, sans-serif;
  }
  .canvas {
    position: relative;
    width: 1200px;
    height: 900px;
  }
  .card {
    position: absolute;
    left: 320px;
    width: 581px;
    height: 358px;
    background: var(--paper);
    box-shadow: 0 1px 3px rgba(0,0,0,0.12);
  }
  .card--front { top: 88px; }
  .card--back { top: 478px; height: 359px; }

  .company-mark {
    position: absolute;
    top: 52px;
    left: 0;
    width: 100%;
    display: flex;
    justify-content: center;
    align-items: center;
    gap: 12px;
  }
  .company-mark__dot {
    width: 22px;
    height: 22px;
    border-radius: 50%;
    background: var(--brand-blue);
  }
  .company-mark__name {
    color: var(--brand-blue);
    font-weight: 700;
    font-size: 30px;
    letter-spacing: 0.5px;
  }

  .manager {
    position: absolute;
    top: 147px;
    width: 100%;
    text-align: center;
  }
  .manager__name {
    margin: 0;
    font-size: 27px;
    font-weight: 700;
    color: var(--ink);
    line-height: 30px;
  }
  .manager__first { color: var(--brand-blue); }
  .manager__title {
    margin: 0;
    font-size: 16px;
    color: var(--ink);
    line-height: 20px;
  }

  .contact-list {
    position: absolute;
    top: 211px;
    width: 100%;
    margin: 0;
    padding: 0;
    list-style: none;
    text-align: center;
    font-size: 16px;
    line-height: 21px;
    color: var(--ink);
  }
  .contact-list__label {
    color: var(--brand-blue);
    font-weight: 700;
  }
  .address {
    position: absolute;
    top: 312px;
    width: 100%;
    margin: 0;
    text-align: center;
    font-size: 16px;
    color: var(--ink);
  }

  .watermark {
    position: absolute;
    inset: 0;
    display: flex;
    justify-content: center;
    align-items: center;
    gap: 20px;
  }
  .watermark__circle {
    width: 130px;
    height: 130px;
    border-radius: 50%;
    background: var(--mist-grey);
  }
  .watermark__name {
    color: var(--mist-grey);
    font-weight: 700;
    font-size: 34px;
  }
</style>
</head>
<body>
  <main class="canvas">
    <section class="card card--front" aria-label="Card front">
      <div class="company-mark">
        <span class="company-mark__dot"></span>
        <span class="company-mark__name">HARBORVIEW ESTATES LLC</span>
      </div>

      <div class="manager">
        <h1 class="manager__name"><span class="manager__first">DANIEL</span> WHITFORD</h1>
        <p class="manager__title">PROPERTY MANAGER</p>
      </div>

      <ul class="contact-list">
        <li><span class="contact-list__label">P:</span> 555-214-7360</li>
        <li><span class="contact-list__label">F:</span> 555-214-7391</li>
        <li><span class="contact-list__label">E:</span> daniel@harborviewestates.us</li>
        <li><span class="contact-list__label">W:</span> www.harborviewestates.us</li>
      </ul>

      <p class="address">2750 Linden Grove Road #B210 Bayside, Ca 92108</p>
    </section>

    <section class="card card--back" aria-label="Card back">
      <div class="watermark">
        <span class="watermark__circle"></span>
        <span class="watermark__name">HARBORVIEW ESTATES</span>
      </div>
    </section>
  </main>
</body>
</html>
```